Business Card Design for Varomir Facility Services

We are looking for a Business Card Design for the Company "Varomir Facility Services."
Front side:
- Company Logo (small)
- Company Name, address, pohone, website and personal data.
- white background, for text e.g. company colors (blue or green like in the logo)
Please use following data:
Company data:
Varomir Facility Services Kostelac
Birkenhaldweg 14
6330 Cham
www.varomir-fs.ch
Person data:
Tarik Kostelac
Geschäftsführer
+41 76 519 47 83
info@varomir-fs.ch
Back side:
could be colored in blue or green
please use a big logo sing and some smaller icons to say what is all beeing offered in facility services, like cleaning, maintenance cleaning
industrial cleaning, caretaking, gardening, disposal. There is no need for everyone of the icons if there are similar or an icon is standing for more of them.
colors to use:
blue: HEX 246BB0
green: HEX 52B33E

```html
<!DOCTYPE html>
<html lang="de">
<head>
<meta charset="utf-8">
<title>Varomir Facility Services – Business Card</title>
<link rel="stylesheet" href="https://fonts.googleapis.com/css2?family=Poppins:wght@400;600&display=swap">
<style>
  :root {
    --blue: #246BB0;
    --green: #52B33E;
    --white: #ffffff;
    --ink: #4a4a4a;
    --rule: #8a8a8a;
    --backdrop: #ecebe8;
  }
  * { margin: 0; padding: 0; box-sizing: border-box; }
  html, body {
    width: 1125px; height: 1200px; overflow: hidden;
    background: var(--backdrop);
    font-family: "Poppins", sans-serif;
  }
  .canvas { position: relative; width: 1125px; height: 1200px; }

  .card {
    position: absolute; left: 150px; width: 825px; height: 472px;
    box-shadow: 0 3px 8px rgba(0,0,0,0.25);
    overflow: hidden;
  }
  .card--front { top: 98px; background: var(--white); }
  .card--back { top: 632px; background: var(--green); }

  /* front */
  .brand {
    position: absolute; right: 36px; top: 150px;
    display: flex; align-items: center; gap: 14px;
  }
  .brand__dot { width: 26px; height: 26px; border-radius: 50%; background: var(--green); flex: none; }
  .brand__name {
    color: var(--blue); font-weight: 600; font-size: 34px; line-height: 1.15;
    text-align: right; white-space: nowrap;
  }
  .person { position: absolute; left: 34px; top: 250px; }
  .person__name { color: var(--blue); font-weight: 600; font-size: 31px; line-height: 1.15; }
  .person__role { color: var(--green); font-size: 21px; line-height: 1.2; }
  .divider {
    position: absolute; left: 34px; right: 38px; top: 332px;
    height: 1px; background: var(--rule);
  }
  .contact { position: absolute; left: 36px; top: 350px; color: var(--ink); font-size: 19px; line-height: 27px; list-style: none; }
  .contact li { display: flex; align-items: center; gap: 10px; }
  .contact svg { width: 16px; height: 18px; flex: none; }
  .address {
    position: absolute; right: 38px; top: 352px; text-align: right;
    color: var(--ink); font-size: 19px; line-height: 26px; font-style: normal;
  }
  .footer-band {
    position: absolute; left: 0; bottom: 0; width: 540px; height: 8px; background: var(--green);
  }
  .web-tab {
    position: absolute; right: 0; bottom: 0; width: 300px; height: 35px;
    background: var(--blue);
    clip-path: polygon(32px 0, 100% 0, 100% 100%, 0 100%);
    color: var(--white); font-size: 19px; letter-spacing: 4.5px;
    display: flex; align-items: center; justify-content: flex-end; padding-right: 20px;
  }

  /* back */
  .brand--back {
    position: absolute; left: 140px; top: 200px; width: 270px;
    display: flex; align-items: center; gap: 12px;
  }
  .brand--back .brand__dot { background: var(--blue); width: 26px; height: 26px; }
  .brand--back .brand__name { color: var(--white); font-size: 28px; text-align: left; }
  .services {
    position: absolute; left: 443px; top: 163px; list-style: none;
    color: var(--white); font-size: 20px; line-height: 24.8px;
  }
  .services li { display: flex; align-items: center; gap: 10px; }
  .services svg { width: 15px; height: 15px; flex: none; }
</style>
</head>
<body>
<main class="canvas">

  <section class="card card--front" aria-label="Vorderseite">
    <div class="brand">
      <span class="brand__name">Varomir<br>Facility Services</span>
      <span class="brand__dot"></span>
    </div>

    <div class="person">
      <h1 class="person__name">Tarik Kostelac</h1>
      <p class="person__role">Geschäftsführer</p>
    </div>

    <div class="divider"></div>

    <ul class="contact">
      <li>
        <svg viewBox="0 0 16 18"><rect x="3" y="1" width="10" height="16" rx="2" fill="none" stroke="#246BB0" stroke-width="2"/><rect x="6" y="13" width="4" height="1.5" fill="#246BB0"/></svg>
        +41 76 519 47 83
      </li>
      <li>
        <svg viewBox="0 0 16 18"><rect x="1" y="5" width="14" height="10" fill="#246BB0"/><path d="M1 5 L8 11 L15 5" fill="none" stroke="#fff" stroke-width="1.3"/></svg>
        info@varomir-fs.ch
      </li>
    </ul>

    <address class="address">
      Varomir Facility Services Kostelac<br>
      Birkenhaldweg 14, 6330 Cham
    </address>

    <div class="footer-band"></div>
    <div class="web-tab">www.varomir-fs.ch</div>
  </section>

  <section class="card card--back" aria-label="Rückseite">
    <div class="brand--back">
      <span class="brand__dot"></span>
      <span class="brand__name">Varomir<br>Facility Services</span>
    </div>

    <ul class="services">
      <li><svg viewBox="0 0 16 16"><path d="M8 0 L9.5 6.5 L16 8 L9.5 9.5 L8 16 L6.5 9.5 L0 8 L6.5 6.5 Z" fill="#fff"/></svg>Cleaning</li>
      <li><svg viewBox="0 0 16 16"><path d="M8 0 L9.5 6.5 L16 8 L9.5 9.5 L8 16 L6.5 9.5 L0 8 L6.5 6.5 Z" fill="#fff"/></svg>Maintenance cleaning</li>
      <li><svg viewBox="0 0 16 16"><path d="M8 0 L9.5 6.5 L16 8 L9.5 9.5 L8 16 L6.5 9.5 L0 8 L6.5 6.5 Z" fill="#fff"/></svg>Industrial cleaning</li>
      <li><svg viewBox="0 0 16 16"><path d="M8 0 L9.5 6.5 L16 8 L9.5 9.5 L8 16 L6.5 9.5 L0 8 L6.5 6.5 Z" fill="#fff"/></svg>Caretaking</li>
      <li><svg viewBox="0 0 16 16"><path d="M8 0 L9.5 6.5 L16 8 L9.5 9.5 L8 16 L6.5 9.5 L0 8 L6.5 6.5 Z" fill="#fff"/></svg>Gardening</li>
      <li><svg viewBox="0 0 16 16"><path d="M8 0 L9.5 6.5 L16 8 L9.5 9.5 L8 16 L6.5 9.5 L0 8 L6.5 6.5 Z" fill="#fff"/></svg>Disposal</li>
    </ul>
  </section>

</main>
</body>
</html>
```